Real Estate Company Looking for Business Card Designs for 3 Executives

Hello!
Thanks so much for considering our project! We are a real estate investment company located in Edmonton, Alberta called Bellhaven Group of Companies. We invest/develop both commercial and residential real estate and are looking to create 3 DOUBLE-SIDED business cards for 3 top executives in the company! (for some reason it won't let us select the double-sided option, but yes, the cards are double sided and would be happy to tip extra)

We have certain guidelines that we want our business cards to for sure follow - the back of the Business card has to be the Black Background Version of the Logo which has already been designed and linked as a file (first file). We want the entire back of the card to simply just be the black background logo. In terms of the front of the card, would like to see a smaller version of the white background logo (linked as the second file) in the top left hand corner - of course, feel free to get creative and we can make revisions together along the way! and Then after that, just text. We want the card to be sharp, clean, easy on the eyes and highly professional looking. We would like the card to include the Full name of the Company (Bellhaven Group of Companies), Name of the Person, Title, Phone, Email. If possible please provide the front part of the card for 3 people:

1) Bellhaven Group of Companies, Liora Quenby, Chief Financial Officer, 780-555-0142, lioraquenby@bellhavengroup.example

2) Bellhaven Group of Companies, Tobias Quenby, Chief Executive Officer, 780-555-0187, tobiasquenby@bellhavengroup.example

3) Bellhaven Group of Companies, Rui Delcourt, Chief Operations Officer, 587-555-0163, ruidelcourt@bellhavengroup.example

Thank you so much for considering our project & we look forward to seeing your designs!

```html
<!DOCTYPE html>
<html lang="en">
<head>
<meta charset="utf-8">
<title>Bellhaven Business Card – Liora Quenby</title>
<link rel="stylesheet" href="https://fonts.googleapis.com/css2?family=Poppins:wght@400;500;700&display=swap">
<style>
  :root {
    --backdrop: #2b2b2b;
    --card-white: #ffffff;
    --card-black: #0d0d0d;
    --ink: #111111;
    --rule: #9a9a9a;
    --paper-text: #ffffff;
  }
  * { margin: 0; padding: 0; box-sizing: border-box; }
  html, body {
    width: 1200px;
    height: 1108px;
    overflow: hidden;
    background: var(--backdrop);
    font-family: "Poppins", sans-serif;
  }
  .stage {
    position: relative;
    width: 1200px;
    height: 1108px;
  }
  .card {
    position: absolute;
    top: 234px;
    width: 400px;
    height: 640px;
    border-radius: 26px;
    overflow: hidden;
  }
  .card--front {
    left: 170px;
    background: var(--card-white);
    color: var(--ink);
    text-align: center;
  }
  .card--back {
    left: 630px;
    background: var(--card-black);
  }
  .brand-name {
    position: absolute;
    top: 170px;
    left: 0;
    right: 0;
    font-size: 36px;
    font-weight: 500;
    letter-spacing: 0.22em;
    padding-left: 0.22em;
    color: var(--ink);
  }
  .holder {
    position: absolute;
    top: 392px;
    left: 0;
    right: 0;
  }
  .holder__name {
    font-size: 26px;
    font-weight: 700;
    letter-spacing: 0.02em;
    line-height: 1.1;
  }
  .holder__title {
    font-size: 17px;
    font-weight: 400;
    margin-top: 2px;
  }
  .contact-rule {
    display: flex;
    align-items: center;
    justify-content: center;
    gap: 10px;
    margin: 14px 28px 10px;
  }
  .contact-rule__line {
    flex: 1;
    height: 1px;
    background: var(--rule);
  }
  .contact-rule__icons { display: flex; gap: 6px; }
  .icon {
    width: 28px;
    height: 28px;
    border-radius: 6px;
    background: var(--ink);
    display: flex;
    align-items: center;
    justify-content: center;
  }
  .contact-list {
    list-style: none;
    font-size: 17px;
    line-height: 1.45;
  }
  .back-pattern {
    position: absolute;
    inset: 0;
    background: linear-gradient(135deg, #2a2a2a 0%, #111 45%, #050505 100%);
  }
  .back-brand {
    position: absolute;
    top: 440px;
    left: 0;
    right: 0;
    text-align: center;
    font-size: 30px;
    font-weight: 500;
    letter-spacing: 0.22em;
    padding-left: 0.22em;
    color: var(--paper-text);
  }
</style>
</head>
<body>
<main class="stage">
  <section class="card card--front" aria-label="Card front">
    <div class="brand-name">BELLHAVEN</div>
    <div class="holder">
      <h1 class="holder__name">LIORA QUENBY</h1>
      <p class="holder__title">Chief Financial Officer</p>
      <div class="contact-rule">
        <span class="contact-rule__line"></span>
        <div class="contact-rule__icons">
          <span class="icon" aria-label="Phone">
            <svg width="16" height="16" viewBox="0 0 24 24"><path fill="#fff" d="M6.6 10.8a15.1 15.1 0 0 0 6.6 6.6l2.2-2.2c.3-.3.7-.4 1-.2 1.1.4 2.3.6 3.6.6.6 0 1 .4 1 1V20c0 .6-.4 1-1 1A17 17 0 0 1 3 4c0-.6.4-1 1-1h3.5c.6 0 1 .4 1 1 0 1.3.2 2.5.6 3.6.1.3 0 .7-.2 1z"/></svg>
          </span>
          <span class="icon" aria-label="Email">
            <svg width="16" height="16" viewBox="0 0 24 24"><rect x="3" y="5" width="18" height="14" rx="1" fill="none" stroke="#fff" stroke-width="2"/><path d="M3 6l9 7 9-7" fill="none" stroke="#fff" stroke-width="2"/></svg>
          </span>
          <span class="icon" aria-label="Website">
            <svg width="16" height="16" viewBox="0 0 24 24"><circle cx="12" cy="12" r="9" fill="none" stroke="#fff" stroke-width="2"/><path d="M3 12h18M12 3c3 3 3 15 0 18M12 3c-3 3-3 15 0 18" fill="none" stroke="#fff" stroke-width="1.6"/></svg>
          </span>
        </div>
        <span class="contact-rule__line"></span>
      </div>
      <ul class="contact-list">
        <li>780-555-0142</li>
        <li>lioraquenby@bellhavengroup.example</li>
        <li>www.bellhavengroup.example</li>
      </ul>
    </div>
  </section>

  <section class="card card--back" aria-label="Card back">
    <div class="back-pattern" role="img" aria-label="Glossy repeating brand pattern on black"></div>
    <div class="back-brand">BELLHAVEN</div>
  </section>
</main>
</body>
</html>
```